Business Card Design Project

Business Card
We are rebranding with a new logo
Industry/Entity Type
Business
Contact Information for Business Card
Dennis Morvale +61 487215963 dennis@quorv.com.au P.O. Box 872 Fernlow QLD 4309
Requirements
Must have
- Logo

```html
<!DOCTYPE html>
<html lang="en">
<head>
<meta charset="utf-8">
<title>Dennis Morvale – Business Card</title>
<link rel="stylesheet" href="https://fonts.googleapis.com/css2?family=Open+Sans:wght@700&family=PT+Sans&family=Libre+Franklin:wght@400;700&display=swap">
<style>
  :root {
    --paper: #f7f7f7;
    --paper-shade: #e6e6e6;
    --ink: #1d1d1d;
    --ink-soft: #7b7b7b;
    --accent-blue: #1a8ad4;
    --brand-blue: #1b6fc4;
    --orange: #ff6a00;
    --cyan: #9ffcff;
    --indigo: #434070;
    --rule: #b9b9b9;
  }
  html, body {
    margin: 0;
    padding: 0;
    overflow: hidden;
    background: #ffffff;
  }
  .card {
    position: relative;
    width: 1200px;
    height: 716px;
    overflow: hidden;
    background: linear-gradient(135deg, var(--paper) 0%, #fbfbfb 45%, var(--paper-shade) 100%);
    font-family: "Libre Franklin", Arial, sans-serif;
  }
  .card__artwork {
    position: absolute;
    left: 0;
    right: 0;
    top: 480px;
    bottom: 0;
    background: linear-gradient(90deg, var(--cyan) 0%, #86d6e8 45%, var(--indigo) 100%);
  }
  .identity {
    position: absolute;
    left: 150px;
    top: 136px;
    width: 400px;
    text-align: center;
  }
  .identity__name {
    margin: 0;
    font-family: "Open Sans", Arial, sans-serif;
    font-weight: 700;
    font-size: 42px;
    letter-spacing: 1px;
    line-height: 1.1;
    color: var(--ink);
    white-space: nowrap;
  }
  .identity__surname { color: var(--ink-soft); }
  .identity__title {
    margin: 2px 0 0;
    font-family: "PT Sans", Arial, sans-serif;
    font-size: 31px;
    color: var(--accent-blue);
    line-height: 1.1;
  }
  .contacts {
    position: absolute;
    left: 164px;
    top: 262px;
    margin: 0;
    padding: 0;
    list-style: none;
  }
  .contacts__item {
    display: flex;
    align-items: flex-start;
    margin-bottom: 17px;
    font-size: 26px;
    line-height: 34px;
    color: var(--ink);
  }
  .contacts__icon {
    flex: none;
    width: 40px;
    height: 40px;
    margin-right: 40px;
  }
  .divider {
    position: absolute;
    left: 641px;
    top: 160px;
    width: 1px;
    height: 212px;
    background: var(--rule);
  }
  .brand {
    position: absolute;
    left: 700px;
    top: 195px;
    width: 300px;
    text-align: center;
    font-family: "Libre Franklin", Arial, sans-serif;
    font-weight: 700;
    color: var(--brand-blue);
  }
  .brand__name {
    display: block;
    font-size: 84px;
    line-height: 1;
    letter-spacing: 1px;
  }
  .brand__suffix {
    display: block;
    margin-top: 16px;
    font-size: 24px;
    letter-spacing: 4px;
  }
</style>
</head>
<body>
<div class="card">
  <div class="card__artwork" role="img" aria-label="Decorative flowing wave artwork in orange, cyan and indigo"></div>

  <header class="identity">
    <h1 class="identity__name">DENNIS <span class="identity__surname">MORVALE</span></h1>
    <p class="identity__title">JOB TITLE</p>
  </header>

  <ul class="contacts">
    <li class="contacts__item">
      <svg class="contacts__icon" viewBox="0 0 40 40" aria-label="Phone">
        <rect width="40" height="40" rx="3" fill="var(--orange)"/>
        <path fill="#fff" d="M13 9c1.2-.6 2.2 0 2.8 1.2l2 4c.5 1 .2 1.9-.6 2.5l-1.6 1.2c1 2.4 2.9 4.5 5.300 5.800l1.3-1.5c.7-.8 1.6-1 2.5-.5l3.9 2.1c1.1.6 1.6 1.7 1 2.8l-1.2 2.1c-.8 1.3-2.300 1.9-3.800 1.5C17.5 28 11.8 22.4 10 15.2c-.4-1.5.3-3 1.6-3.9z"/>
      </svg>
      <span>+61 487215963</span>
    </li>
    <li class="contacts__item">
      <svg class="contacts__icon" viewBox="0 0 40 40" aria-label="Email">
        <rect width="40" height="40" rx="3" fill="var(--orange)"/>
        <rect x="6" y="11" width="24" height="17" fill="none" stroke="#fff" stroke-width="2"/>
        <path d="M6 11 L18 21 L30 11" fill="none" stroke="#fff" stroke-width="2"/>
        <circle cx="30" cy="28" r="5" fill="none" stroke="#fff" stroke-width="2"/>
      </svg>
      <span>dennis@quorv.com.au</span>
    </li>
    <li class="contacts__item">
      <svg class="contacts__icon" viewBox="0 0 40 40" aria-label="Post box">
        <rect width="40" height="40" rx="3" fill="var(--orange)"/>
        <path fill="#fff" d="M11 14a9 9 0 0 1 18 0v17H11z"/>
        <rect x="14" y="17" width="12" height="3" fill="var(--orange)"/>
        <rect x="14" y="23" width="12" height="2" fill="var(--orange)"/>
      </svg>
      <span>P.O. Box 872 Fernlow<br>QLD 4309</span>
    </li>
  </ul>

  <div class="divider"></div>

  <div class="brand">
    <span class="brand__name">Quorv</span>
    <span class="brand__suffix">INTERNATIONAL</span>
  </div>
</div>
</body>
</html>
```